Website Design for Employee Moral and Happiness Company

Looking for a clean website design that explains our features in a step by step manner so our visitors know exactly what our site does before logging in.

The site is called "Velrato". See logo design and video for a sample of style and an overview of what we do.

Target Market(s)

Business owners that are looking to retain employees.

Number of Pages Required

1 page

```html
<!DOCTYPE html>
<html lang="en">
<head>
<meta charset="utf-8">
<title>Velrato – Company Morale</title>
<link href="https://fonts.googleapis.com/css2?family=Lora:wght@500;700&family=Roboto:wght@400;500;700&display=swap" rel="stylesheet">
<style>
:root{
  --orange:#e05a1a;
  --orange-dark:#c94c12;
  --ink:#111111;
  --text:#555555;
  --muted:#777777;
  --white:#ffffff;
  --black:#000000;
  --line:#e2e2e2;
}
*{box-sizing:border-box;margin:0;padding:0}
html,body{width:1200px;height:3992px;overflow:hidden;background:var(--white)}
body{position:relative;font-family:'Roboto',Arial,sans-serif;color:var(--text)}
.abs{position:absolute}
.serif{font-family:'Lora',Georgia,serif}
.smile{display:block;width:26px;height:8px;border-bottom:3px solid var(--orange);border-radius:0 0 20px 20px;margin:2px auto 0}
/* header */
.header{left:0;top:0;width:1200px;height:70px;background:var(--white)}
.brand{left:110px;top:10px;font-family:'Lora',Georgia,serif;font-weight:700;font-size:44px;color:var(--ink);line-height:44px}
.nav{left:395px;top:28px;display:flex;gap:32px;font-size:13px;font-weight:500;color:var(--ink)}
.nav .active{color:var(--orange)}
.call-icon{left:865px;top:20px;width:34px;height:34px;border:2px solid var(--orange);border-radius:50%}
.call{left:918px;top:19px;font-size:11px;font-weight:700;color:var(--ink)}
.call b{display:block;font-size:21px;color:var(--orange);margin-top:2px}
/* hero */
.hero{left:0;top:70px;width:1200px;height:660px}
.hero-photo{width:100%;height:100%;background:linear-gradient(100deg,#6b6b68 0%,#3d3f3e 45%,#2c2e2d 100%)}
.hero-title{left:600px;top:222px;width:560px;font-size:46px;font-weight:700;line-height:52px;color:var(--white)}
.hero-text{left:600px;top:353px;width:520px;font-size:16px;font-weight:700;line-height:25px;color:var(--white)}
.btn{background:var(--orange);color:var(--white);font-size:14px;font-weight:700;display:flex;align-items:center;gap:10px;justify-content:center}
.hero-btn{left:600px;top:430px;width:162px;height:46px}
/* about */
.about-title{left:132px;top:752px;font-size:34px;color:var(--ink)}
.about-title .smile{margin:0}
.about-text{left:132px;top:820px;width:440px;font-size:14px;line-height:26px;text-align:justify}
.about-btn{left:132px;top:1068px;width:145px;height:44px}
.about-ring{left:660px;top:720px;width:414px;height:434px;border-top:10px solid var(--orange);border-radius:50%}
.about-photo{left:662px;top:736px;width:410px;height:410px;border-radius:50%;background:linear-gradient(160deg,#c9c2b8,#6f6656 60%,#3e3a33)}
/* features */
.features-title{left:0;top:1296px;width:1200px;text-align:center;font-size:35px;color:var(--white)}
.features-text{left:100px;top:1370px;width:1000px;text-align:center;font-size:15px;line-height:22px;color:var(--white)}
.step{width:280px;height:280px;border-radius:50%;background:var(--white);text-align:center;overflow:hidden}
.step-big{background:var(--white);width:318px;height:318px}
.step .num{position:absolute;left:0;right:0;top:100px;font-size:110px;font-weight:700;color:#eeeeee;line-height:110px}
.step .ico{position:absolute;left:50%;transform:translateX(-50%);top:36px}
.step h3{position:absolute;left:0;right:0;top:130px;font-size:15px;font-weight:500;color:var(--ink)}
.step .bar{position:absolute;left:50%;top:158px;width:28px;height:2px;margin-left:-14px;background:var(--orange)}
.step p{position:absolute;left:18px;right:18px;top:172px;font-size:11.5px;line-height:16px;color:var(--muted)}
/* services */
.services-title{left:0;top:1888px;width:1200px;text-align:center;font-size:35px;color:var(--ink)}
.service{top:1982px;width:234px;height:258px;border-radius:8px;overflow:hidden}
.service .img{width:100%;height:100%}
.service span{position:absolute;left:38px;bottom:28px;font-family:'Lora',Georgia,serif;font-weight:700;font-size:15px;color:var(--white)}
.service i{position:absolute;right:46px;bottom:29px;width:14px;height:14px;border-radius:50%;background:var(--white)}
/* clients */
.clients{left:0;top:2325px;width:1200px;height:420px;background:var(--orange)}
.clients-title{left:0;top:2378px;width:1200px;text-align:center;font-size:35px;color:var(--white)}
.clients-title .smile{border-color:var(--white)}
.quote{top:2472px;width:312px;height:122px;background:var(--white);border-radius:14px;padding:22px 24px;font-size:13.5px;font-style:italic;line-height:20px;color:var(--muted)}
.quote b{position:absolute;right:28px;bottom:14px;font-family:'Lora',Georgia,serif;font-size:44px;font-style:normal;color:var(--orange);line-height:30px}
.person{top:2622px;display:flex;align-items:center;gap:16px;color:var(--white);font-size:14px}
.person .av{width:58px;height:58px;border-radius:50%;background:#d9c7b5;border:3px solid #f0e0d0}
.person strong{display:block;font-weight:700}
/* blog */
.blog-title{left:0;top:2806px;width:1200px;text-align:center;font-size:35px;color:var(--ink)}
.post{width:482px;height:222px;background:var(--white);box-shadow:0 2px 10px rgba(0,0,0,.12)}
.post .img{position:absolute;left:0;top:0;width:220px;height:100%;border-right:4px solid var(--orange)}
.post h4{position:absolute;left:244px;top:40px;font-size:14px;font-weight:700;color:var(--ink)}
.post .bar{position:absolute;left:244px;top:66px;width:38px;height:2px;background:var(--orange)}
.post p{position:absolute;left:244px;top:83px;width:210px;font-size:14px;line-height:21px;color:var(--muted)}
.post .date{position:absolute;left:244px;top:166px;font-size:12px;font-weight:700;color:#333;display:flex;gap:10px;align-items:center}
.post .date i{width:11px;height:11px;background:var(--orange);border-radius:2px}
.learn{left:0;top:3440px;width:1200px;text-align:center;font-size:13px;font-weight:700;color:#8a6a3a;text-decoration:underline}
/* footer */
.footer-bg{left:0;top:3470px;width:1200px;height:522px}
.f-head{font-size:15px;font-weight:700;color:var(--white)}
.field{background:var(--white);font-size:14px;color:#777;padding:13px 8px}
.submit{left:112px;top:3855px;width:117px;height:42px;border-radius:22px}
.info{color:var(--white);font-size:14px;line-height:22px}
.info-ico{width:28px;height:28px;border-radius:50%;background:var(--white)}
.links{left:952px;top:3664px;color:var(--white);font-size:14px;line-height:34px}
.social{top:3834px;width:26px;height:26px;border-radius:50%}
.rule{left:112px;top:3925px;width:976px;height:1px;background:#333}
.copy{top:3952px;color:var(--white);font-size:13px}
</style>
</head>
<body>

<!-- header -->
<div class="abs header"></div>
<div class="abs brand">Velrato</div>
<nav class="abs nav"><span class="active">HOME</span><span>ABOUT</span><span>OUR SERVICES</span><span>REVIEWS</span><span>CONTACT</span></nav>
<div class="abs call-icon"><svg width="30" height="30" viewBox="0 0 30 30"><path d="M10 8l3 3-2 2a9 9 0 0 0 6 6l2-2 3 3-2 2c-6 0-12-6-12-12z" fill="none" stroke="#e05a1a" stroke-width="1.6"/></svg></div>
<div class="abs call">CALL US TODAY !<b>+ 1 555 014 2290</b></div>

<!-- hero -->
<div class="abs hero">
  <div class="hero-photo" role="img" aria-label="Smiling woman working at a laptop in a bright office"></div>
</div>
<svg class="abs" style="left:0;top:580px" width="1200" height="160" viewBox="0 0 1200 160">
  <path d="M0 140 Q600 -20 1200 140 L1200 160 L0 160Z" fill="#e05a1a"/>
  <path d="M0 146 Q600 0 1200 146 L1200 160 L0 160Z" fill="#ffffff"/>
</svg>
<h1 class="abs hero-title serif">Company Morale : What Makes Employees Happy</h1>
<p class="abs hero-text">Lorem ipsum dolor sit amet, consectetur adipiscing elit, sed do eiusmod tempor incididunt ut labore</p>
<div class="abs btn hero-btn">GET STARTED <span>&#10140;</span></div>

<!-- about -->
<h2 class="abs about-title serif">About Us<span class="smile"></span></h2>
<p class="abs about-text">Sed ut perspiciatis unde omnis iste natus error sit voluptatem accusantium doloremque laudantium, totam rem aperiam, eaque ipsa quae ab illo inventore veritatis et quasi architecto beatae vitae dicta sunt explicabo. Nemo enim ipsam voluptatem quia voluptas sit aspernatur aut odit aut fugit, sed quia consequuntur magni dolores eos qui ratione voluptatem sequi nesciunt. Neque porro quisquam est, qui dolorem ipsum quia dolor sit amet, consectetur, adipisci velit, sed quia non numquam eius modi tempora incidunt ut labore et dolore magnam aliquam quaerat</p>
<div class="abs btn about-btn">LEARN MORE <span>&#10140;</span></div>
<div class="abs about-ring"></div>
<div class="abs about-photo" role="img" aria-label="Group of smiling coworkers standing together"></div>

<!-- features band -->
<svg class="abs" style="left:0;top:1150px" width="1200" height="760" viewBox="0 0 1200 760">
  <path d="M0 0 Q600 190 1200 0 L1200 740 Q600 600 0 740Z" fill="#e05a1a"/>
  <path d="M0 0 Q600 190 1200 0 L1200 8 Q600 198 0 28Z" fill="#000000"/>
  <path d="M0 740 Q600 560 1200 740 L1200 750 Q600 576 0 760Z" fill="#000000"/>
  <path d="M0 760 Q600 576 1200 750 L1200 760Z" fill="#ffffff"/>
</svg>
<h2 class="abs features-title serif">Our Features<span class="smile" style="border-color:#fff"></span></h2>
<p class="abs features-text">Lorem ipsum dolor sit amet, consectetur adipiscing elit, sed do eiusmod tempor incididunt ut labore et dolore magna aliqua. Ut enim ad minim veniam, quis nostrud exercitation ullamco laboris nisi ut aliquip ex ea commodo consequat.</p>

<div class="abs step" style="left:166px;top:1462px">
  <div class="num">01</div>
  <svg class="ico" width="80" height="70" viewBox="0 0 80 70"><circle cx="40" cy="16" r="12" fill="none" stroke="#e05a1a" stroke-width="5"/><path d="M8 58l16-16h32l16 16-12 8-20-10-20 10z" fill="#e05a1a"/></svg>
  <h3>STEP - 01</h3><div class="bar"></div>
  <p>Lorem ipsum dolo siamet, consectetur adipiscing elit, sed do eiusmod tempor incididunt ut labore</p>
</div>
<div class="abs step step-big" style="left:441px;top:1442px">
  <div class="num" style="top:110px">02</div>
  <svg class="ico" width="90" height="80" viewBox="0 0 90 80" style="top:40px"><circle cx="25" cy="18" r="10" fill="#e05a1a"/><circle cx="65" cy="18" r="10" fill="#e05a1a"/><circle cx="45" cy="28" r="12" fill="#e05a1a"/><path d="M5 60c0-14 10-22 20-22s14 6 14 6M85 60c0-14-10-22-20-22s-14 6-14 6" fill="#e05a1a"/><path d="M20 76c0-18 12-30 25-30s25 12 25 30z" fill="#e05a1a"/></svg>
  <h3 style="top:148px">STEP - 02</h3><div class="bar" style="top:176px"></div>
  <p style="top:190px;left:50px;right:50px">Lorem ipsum dolo siamet, consectetur adipiscing elit, sed do eiusmod tempor incididunt ut labore</p>
</div>
<div class="abs step" style="left:756px;top:1462px">
  <div class="num">03</div>
  <svg class="ico" width="80" height="70" viewBox="0 0 80 70"><circle cx="20" cy="12" r="7" fill="#e05a1a"/><circle cx="40" cy="10" r="8" fill="#e05a1a"/><circle cx="60" cy="12" r="7" fill="#e05a1a"/><rect x="10" y="24" width="20" height="40" rx="5" fill="#e05a1a"/><rect x="30" y="22" width="20" height="46" rx="5" fill="#e05a1a"/><rect x="50" y="24" width="20" height="40" rx="5" fill="#e05a1a"/></svg>
  <h3>STEP - 03</h3><div class="bar"></div>
  <p>Lorem ipsum dolo siamet, consectetur adipiscing elit, sed do eiusmod tempor incididunt ut labore</p>
</div>

<!-- services -->
<h2 class="abs services-title serif">Our Services<span class="smile"></span></h2>
<div class="abs service" style="left:103px"><div class="img" role="img" aria-label="Team meeting around a long table" style="background:linear-gradient(180deg,#b8b2a6,#5b5750)"></div><span>LOREM IPSUM</span><i></i></div>
<div class="abs service" style="left:357px"><div class="img" role="img" aria-label="Colleagues laughing together at work" style="background:linear-gradient(180deg,#c9c9c6,#4e4f50)"></div><span>LOREM IPSUM</span><i></i></div>
<div class="abs service" style="left:610px"><div class="img" role="img" aria-label="Team reviewing documents at a desk" style="background:linear-gradient(180deg,#d0cfcb,#56524c)"></div><span>LOREM IPSUM</span><i></i></div>
<div class="abs service" style="left:864px"><div class="img" role="img" aria-label="Business people shaking hands in an office" style="background:linear-gradient(180deg,#a7adb4,#2f3540)"></div><span>LOREM IPSUM</span><i></i></div>

<!-- clients -->
<div class="abs clients"></div>
<h2 class="abs clients-title serif">What Our Clients Say<span class="smile"></span></h2>
<div class="abs quote" style="left:107px">Sed ut perspiciatis unde omnis istenatus error sit voluptatem accusandoloremque laudantium, totam aperiam<b>&ldquo;</b></div>
<div class="abs quote" style="left:444px">Sed ut perspiciatis unde omnis istenatus error sit voluptatem accusandoloremque laudantium, totam aperiam<b>&ldquo;</b></div>
<div class="abs quote" style="left:781px">Sed ut perspiciatis unde omnis istenatus error sit voluptatem accusandoloremque laudantium, totam aperiam<b>&ldquo;</b></div>
<div class="abs person" style="left:120px"><div class="av" role="img" aria-label="Client portrait"></div><div><strong>JOHN DOE</strong>Businessman</div></div>
<div class="abs person" style="left:457px"><div class="av" role="img" aria-label="Client portrait"></div><div><strong>JOHN DOE</strong>Businessman</div></div>
<div class="abs person" style="left:794px"><div class="av" role="img" aria-label="Client portrait"></div><div><strong>JOHN DOE</strong>Businessman</div></div>

<!-- blog -->
<h2 class="abs blog-title serif">Latest Blog<span class="smile"></span></h2>
<article class="abs post" style="left:110px;top:2900px"><div class="img" role="img" aria-label="Colleagues discussing work at a laptop" style="background:linear-gradient(160deg,#bcb6ad,#4d4a45)"></div><h4>LOREM IPSUM DOLOR SIT AMET</h4><div class="bar"></div><p>Sed ut perspiciatis unde omnis iste natus error sit voluptatem accusantium</p><div class="date"><i></i>20 JUNE , 2021</div></article>
<article class="abs post" style="left:607px;top:2900px"><div class="img" role="img" aria-label="Business handshake across a table" style="background:linear-gradient(160deg,#d4d4d2,#5a5855)"></div><h4>LOREM IPSUM DOLOR SIT AMET</h4><div class="bar"></div><p>Sed ut perspiciatis unde omnis iste natus error sit voluptatem accusantium</p><div class="date"><i></i>20 JUNE , 2021</div></article>
<article class="abs post" style="left:110px;top:3148px"><div class="img" role="img" aria-label="Team group photo in an office" style="background:linear-gradient(160deg,#a9b3b8,#3a3d40)"></div><h4>LOREM IPSUM DOLOR SIT AMET</h4><div class="bar"></div><p>Sed ut perspiciatis unde omnis iste natus error sit voluptatem accusantium</p><div class="date"><i></i>20 JUNE , 2021</div></article>
<article class="abs post" style="left:607px;top:3148px"><div class="img" role="img" aria-label="Two colleagues working at a computer" style="background:linear-gradient(160deg,#c5c3bf,#4a4744)"></div><h4>LOREM IPSUM DOLOR SIT AMET</h4><div class="bar"></div><p>Sed ut perspiciatis unde omnis iste natus error sit voluptatem accusantium</p><div class="date"><i></i>20 JUNE , 2021</div></article>
<div class="abs learn">LEARN MORE &nbsp;&raquo;</div>

<!-- footer -->
<svg class="abs footer-bg" width="1200" height="522" viewBox="0 0 1200 522">
  <path d="M0 0 Q600 200 1200 0 L1200 522 L0 522Z" fill="#000000"/>
  <path d="M120 58 Q600 180 1080 58 Q600 166 120 58Z" fill="#e05a1a"/>
</svg>
<div class="abs f-head" style="left:112px;top:3630px">GET IN TOUCH</div>
<div class="abs field" style="left:112px;top:3666px;width:222px;height:44px">Name</div>
<div class="abs field" style="left:345px;top:3666px;width:222px;height:44px">Phone</div>
<div class="abs field" style="left:112px;top:3718px;width:455px;height:44px">Email</div>
<div class="abs field" style="left:112px;top:3770px;width:455px;height:76px;padding-top:8px">Message</div>
<div class="abs btn submit">SUBMIT</div>

<div class="abs f-head" style="left:628px;top:3632px;font-size:13px">CONTACT INFO</div>
<div class="abs info-ico" style="left:628px;top:3668px"></div>
<div class="abs info" style="left:674px;top:3666px;font-size:13.5px">129 . Velrato lorem Ipsum<br>United States</div>
<div class="abs info-ico" style="left:628px;top:3724px"></div>
<div class="abs info" style="left:674px;top:3726px;font-size:15px;font-weight:700">+1 555 014 2290</div>
<div class="abs info-ico" style="left:628px;top:3776px"></div>
<div class="abs info" style="left:674px;top:3779px">info@velrato.com</div>
<div class="abs f-head" style="left:628px;top:3836px">STAY CONNECTED</div>
<div class="abs social" style="left:805px;background:#3b5bb0"></div>
<div class="abs social" style="left:842px;background:#2b9de0"></div>
<div class="abs social" style="left:880px;background:#d63b2a"></div>
<div class="abs social" style="left:918px;background:#1d6fb0"></div>
<div class="abs social" style="left:956px;background:#d0241d"></div>

<div class="abs f-head" style="left:952px;top:3632px;font-size:13px">QUICK LINKS</div>
<div class="abs links">&raquo;&nbsp;&nbsp; Home<br>&raquo;&nbsp;&nbsp; About Us<br>&raquo;&nbsp;&nbsp; Our Features<br>&raquo;&nbsp;&nbsp; Latest Blog<br>&raquo;&nbsp;&nbsp; Contact Us</div>

<div class="abs rule"></div>
<div class="abs copy" style="left:112px">&copy; 2022 Velrato. All Rights reserved</div>
<div class="abs copy" style="left:907px">Terms Of Use &nbsp;|&nbsp; Privacy Policy</div>

</body>
</html>
```